Cyber Security Site Design (Products & Consulting)

I need my website redesigned to be engaging, clean, efficient and modern. My company (when its up and running) is going to be concentrated on two things: a few specific products for cyber security as well as cyber security consulting services. The background I bring to the field is having worked with small companies all the way to the largest government organizations and advising them on their security posture and how to improve it. We need the ability to add products and services easily.

For a sample product, you can use either Tarnet (http://www.tarnet-relay.org/) or Verodyne Ashmantle (https://www.verodyne.com/products/relay-hx-and-fortified-edge-portal).

It will replace https://lumerafieldworks.com/

Target Market(s)

Cyber Security professionals in all verticals

Coding

Coded - Design and coding required

Number of Pages Required

4 page

Font styles to use
Sans Serif

Colors
6b449b

Requirements
Must have
• Ability to easily modify
• Have main page
• Have product specific pages
• Have consulting services pages
• Have executive team information
• Clean, modern design
• Usage of the logo and its color scheme
Nice to have
• I like the idea of a left collapsed sidebar (so icons only) that can expand for text.
• I am also open to a very unique landing page, possibly a shape in the middle (hexagons maybe?) with each of the options there.
Should not have
• Nothing that looks like it came out of a hacker movie

```html
<!DOCTYPE html>
<html lang="en">
<head>
<meta charset="utf-8">
<title>Lumera Fieldworks — Cyber Security Consulting</title>
<link rel="stylesheet" href="https://fonts.googleapis.com/css2?family=Bai+Jamjuree:wght@600;700&family=Mulish:wght@400;600;700;800&display=swap">
<style>
:root{
  --purple:#6b449b;
  --purple-dark:#4f2f7a;
  --purple-soft:#8a67b8;
  --ink:#2b2b33;
  --text:#55555f;
  --muted:#9a9aa6;
  --line:#e4e4ea;
  --panel:#f5f6f9;
  --white:#ffffff;
  --orange:#f29a4b;
  --night:#121826;
  --heading:"Bai Jamjuree",sans-serif;
  --body:"Mulish",sans-serif;
}
*{box-sizing:border-box;margin:0;padding:0}
html,body{width:1200px;height:4500px;overflow:hidden;background:var(--white)}
body{font-family:var(--body);color:var(--text);position:relative}
.section{position:absolute;left:0;width:1200px}
.section-title{font-family:var(--heading);font-weight:700;color:var(--ink);font-size:32px;letter-spacing:1px;text-align:center;text-transform:uppercase}
.title-mark{display:block;width:14px;height:14px;border:3px solid var(--purple);border-radius:3px;margin:12px auto 0}

/* header */
.site-header{top:0;height:120px;background:var(--white);box-shadow:0 2px 8px rgba(0,0,0,.06);z-index:2}
.brand{position:absolute;left:36px;top:22px;display:flex;align-items:center;gap:14px}
.brand-square{width:54px;height:54px;background:var(--purple);border-radius:8px}
.brand-name{font-family:var(--body);font-weight:800;font-size:30px;color:var(--purple);letter-spacing:1px;line-height:1}
.contact-bar{position:absolute;right:110px;top:16px;display:flex;align-items:center;gap:16px;font-size:13px;color:var(--ink)}
.contact-item{display:flex;align-items:center;gap:8px}
.contact-icon{width:24px;height:24px;border-radius:50%;background:var(--purple);display:flex;align-items:center;justify-content:center}
.social{display:flex;gap:6px}
.social span{width:22px;height:22px;border-radius:50%}
.main-nav{position:absolute;right:100px;top:78px;display:flex;gap:50px;font-size:13px;font-weight:700;color:var(--ink)}
.main-nav .active{color:var(--purple);border-bottom:2px solid var(--purple);padding-bottom:6px}

/* hero */
.hero{top:120px;height:576px}
.hero-visual{position:absolute;inset:0;background:radial-gradient(circle at 38% 40%,#3aa6e8 0%,#174a8a 22%,#0a1c3d 55%,#050b1a 100%)}
.hero-copy{position:absolute;left:660px;top:175px;width:400px;color:var(--white)}
.hero-copy h1{font-family:var(--heading);font-weight:600;font-size:34px;letter-spacing:6px;line-height:1.2}
.hero-copy p{font-size:13px;line-height:1.6;margin-top:14px;color:#d5dbe8}
.hero-btn{display:inline-block;margin-top:20px;border:1px solid #fff;padding:8px 30px;font-size:13px;letter-spacing:1px;color:#fff}
.hero-arrow{position:absolute;top:250px}
.hero-notch{position:absolute;left:550px;bottom:-44px;width:100px;height:100px;border-radius:50%;background:var(--white);display:flex;align-items:flex-start;justify-content:center;padding-top:18px}

/* about */
.about{top:696px;height:294px;padding-top:52px}
.about-text{width:1000px;margin:26px auto 0;text-align:center;font-size:15px;line-height:1.9;color:var(--text)}
.about-text p+p{margin-top:8px}

/* services */
.services{top:990px;height:700px;background:var(--panel);padding-top:70px}
.service-grid{position:absolute;left:144px;top:180px;width:912px;display:grid;grid-template-columns:repeat(3,304px);grid-template-rows:240px 240px}
.service{text-align:center;padding:34px 30px 0;border-color:var(--line);border-style:solid;border-width:0}
.service:nth-child(-n+3){border-bottom-width:1px}
.service:nth-child(3n+2){border-left-width:1px;border-right-width:1px}
.service h3{font-family:var(--heading);font-weight:700;font-size:15px;color:var(--ink);margin-top:14px;text-transform:uppercase}
.service p{font-size:12.5px;line-height:1.55;margin-top:8px}
.service.featured{background:var(--purple);color:#e8ddf6;box-shadow:0 12px 28px rgba(107,68,155,.35);margin:-14px 14px 34px}
.service.featured h3{color:#fff}
.service-icon{display:block;margin:0 auto}

/* products */
.products{top:1690px;height:520px;padding-top:76px}
.product-row{position:absolute;left:144px;top:180px;display:flex;gap:40px}
.product-card{width:441px;height:270px;background:#fff;box-shadow:0 4px 18px rgba(0,0,0,.08);display:flex;gap:24px;padding:30px 26px;border-radius:4px}
.product-box{width:150px;height:210px;flex:none;border-radius:3px}
.product-card h3{font-family:var(--heading);font-weight:700;color:var(--purple);font-size:22px;letter-spacing:1px}
.product-card p{font-size:12.5px;line-height:1.6;margin-top:10px}
.product-link{display:block;margin-top:12px;font-size:13px;color:var(--purple);font-weight:700}

/* security callout */
.callout{top:2210px;height:420px;background:var(--panel)}
.callout-visual{position:absolute;left:156px;top:70px;width:285px;height:285px;border-radius:50% 0 50% 50%;background:linear-gradient(135deg,#e8e2d8,#b9a996 55%,#6d6052)}
.callout-copy{position:absolute;left:492px;top:98px;width:560px}
.callout-copy h2{font-family:var(--heading);font-weight:700;font-size:28px;color:var(--ink);letter-spacing:1px}
.callout-copy .lead{font-weight:800;font-size:16px;color:var(--ink);margin-top:10px}
.callout-copy p{font-size:13px;line-height:1.7;margin-top:12px}
.cta{display:inline-flex;align-items:center;gap:10px;margin-top:26px;background:var(--purple);color:#fff;font-weight:800;font-size:15px;letter-spacing:1px;padding:0 26px 0 0;height:42px}
.cta-square{width:42px;height:42px;background:var(--ink)}

/* team */
.team{top:2630px;height:540px;padding-top:104px}
.team-row{position:absolute;left:141px;top:205px;display:flex;gap:12px}
.member{width:219px;height:225px;border:1px solid var(--line);text-align:center;padding-top:30px;background:#fff}
.member-photo{width:106px;height:106px;border-radius:50%;margin:0 auto;background:linear-gradient(160deg,#d9d3cc,#8c8178)}
.member h3{font-weight:800;font-size:15px;color:var(--ink);margin-top:18px}
.member span{font-size:12px;text-transform:uppercase}
.pager{position:absolute;left:573px;top:452px;display:flex;gap:10px}
.pager span{width:22px;height:22px;border-radius:50%;border:1px solid #c7c7cf}
.pager .on{border-color:var(--ink)}

/* stats */
.stats{top:3170px;height:245px;background:linear-gradient(120deg,#5a3786,#7b54ad 50%,#5e3b8d)}
.stat-row{position:absolute;left:140px;top:40px;display:flex}
.stat{width:230px;text-align:center;color:#fff}
.stat strong{display:block;font-family:var(--body);font-weight:600;font-size:50px;line-height:1;margin-top:10px}
.stat span{font-size:14px;font-weight:700;text-transform:uppercase;letter-spacing:.5px}

/* reviews */
.reviews{top:3415px;height:495px;padding-top:72px}
.review{position:absolute;text-align:center;font-size:12.5px;line-height:1.6}
.review h3{font-family:var(--body);font-weight:800;font-size:16px;color:var(--purple);margin-top:4px}
.review.main{left:414px;top:170px;width:372px;height:249px;background:#fff;box-shadow:0 6px 24px rgba(0,0,0,.1);padding:28px 30px}
.review.side{top:200px;width:300px;opacity:.35}
.review .who{font-weight:800;color:var(--ink);margin-top:12px}
.review .role{font-size:11px;text-transform:uppercase}
.quote-mark{font-family:var(--heading);font-size:36px;color:var(--purple);line-height:.8}

/* location */
.location{top:3910px;height:530px}
.location-visual{position:absolute;inset:0;background:linear-gradient(135deg,#1b2436,#0c111d 60%,#1a2030)}
.location h2{position:absolute;left:228px;top:80px;font-family:var(--heading);font-weight:700;font-size:32px;color:#fff;letter-spacing:1px}
.location .sub{position:absolute;left:228px;top:128px;width:300px;font-size:13px;line-height:1.6;color:#c9cfdb}
.map{position:absolute;left:228px;top:185px;width:438px;height:225px;background:linear-gradient(140deg,#eef0ec,#dfe3da 60%,#cfd6cd)}
.help{position:absolute;left:666px;top:146px;width:310px;height:264px;background:#fff;border:3px solid var(--purple);padding:18px 22px}
.help h3{font-family:var(--heading);font-weight:700;font-size:28px;color:var(--purple);letter-spacing:1px}
.help small{font-size:11px;display:block}
.field{border-bottom:1px solid var(--line);font-size:11px;color:var(--muted);padding:10px 0 6px}
.submit{display:inline-flex;align-items:center;gap:8px;margin-top:18px;background:var(--purple);color:#fff;font-weight:800;font-size:13px;height:30px;padding-right:16px}
.submit i{width:30px;height:30px;background:var(--ink)}

/* footer */
.site-footer{top:4440px;height:60px;background:var(--purple);color:#fff;font-size:12px;display:flex;align-items:center;justify-content:space-between;padding:0 150px}
.site-footer .social span{background:rgba(255,255,255,.9);width:24px;height:24px}
</style>
</head>
<body>

<header class="section site-header">
  <div class="brand"><span class="brand-square"></span><span class="brand-name">LUMERA FIELDWORKS</span></div>
  <div class="contact-bar">
    <div class="contact-item"><span class="contact-icon"><svg width="12" height="12" viewBox="0 0 24 24"><path d="M6.6 10.8a15.1 15.1 0 0 0 6.6 6.6l2.2-2.2a1 1 0 0 1 1-.25 11.4 11.4 0 0 0 3.6.57 1 1 0 0 1 1 1V20a1 1 0 0 1-1 1A17 17 0 0 1 3 4a1 1 0 0 1 1-1h3.5a1 1 0 0 1 1 1c0 1.25.2 2.45.57 3.57a1 1 0 0 1-.25 1z" fill="#fff"/></svg></span>(012) 555 0147</div>
    <div class="contact-item"><span class="contact-icon"><svg width="12" height="12" viewBox="0 0 24 24"><rect x="3" y="6" width="18" height="12" rx="1" fill="none" stroke="#fff" stroke-width="2"/><path d="M3 7l9 6 9-6" fill="none" stroke="#fff" stroke-width="2"/></svg></span>inquiry@lumerafieldworks.com</div>
    <div class="social"><span style="background:#3b5a98"></span><span style="background:#d9302b"></span><span style="background:#2aa3ef"></span><span style="background:#1b78b4"></span></div>
  </div>
  <nav class="main-nav"><span class="active">HOME</span><span>SERVICES</span><span>OUR TEAM</span><span>PRODUCTS</span><span>CONTACT US</span></nav>
</header>

<section class="section hero">
  <div class="hero-visual" role="img" aria-label="Open hand holding a glowing blue digital security globe on a dark background"></div>
  <div class="hero-copy">
    <h1>CYBER SECURITY<br>CONSULTING</h1>
    <p>Ullamcorper sed eget tempor cursus neque mi consectetur in a ultricies massa est sed nisl. Class aptent taciti sociosqu.</p>
    <span class="hero-btn">READ MORE</span>
  </div>
  <svg class="hero-arrow" style="left:78px" width="24" height="44" viewBox="0 0 24 44"><path d="M20 2L4 22l16 20" fill="none" stroke="#fff" stroke-width="2"/></svg>
  <svg class="hero-arrow" style="right:78px" width="24" height="44" viewBox="0 0 24 44"><path d="M4 2l16 20L4 42" fill="none" stroke="#fff" stroke-width="2"/></svg>
  <div class="hero-notch"><svg width="34" height="20" viewBox="0 0 34 20"><path d="M3 3l14 14L31 3" fill="none" stroke="#333" stroke-width="3"/></svg></div>
</section>

<section class="section about">
  <h2 class="section-title">About Us</h2><span class="title-mark"></span>
  <div class="about-text">
    <p>We are a company that takes its roots from the idea of providing appropriate and creative solutions for cyber security operations, development and management. We have a mission first mindset for our clients and their objectives.</p>
    <p>We are located in the Brennick / Halvern Valley area but are able to work with clients world-wide. Please contact us for any inquiries you may have and we will be glad to assist you in any way possible.</p>
  </div>
</section>

<section class="section services">
  <h2 class="section-title">Cyber Security Consulting Services</h2><span class="title-mark"></span>
  <div class="service-grid">
    <div class="service">
      <svg class="service-icon" width="60" height="60" viewBox="0 0 60 60" fill="none" stroke="#6b449b" stroke-width="2"><circle cx="30" cy="18" r="10"/><path d="M10 54c2-14 10-20 20-20s18 6 20 20"/><path d="M30 34v12"/></svg>
      <h3>Virtual CISO / vISO</h3>
      <p>Adipiscing elit sed autem eiusmode mporal laboratories dolore magna aliqua rerum adim minim veniam quis.</p>
    </div>
    <div class="service featured">
      <svg class="service-icon" width="60" height="60" viewBox="0 0 60 60" fill="none" stroke="#fff" stroke-width="2"><rect x="18" y="18" width="24" height="24" rx="3"/><path d="M24 18v-8M30 18v-8M36 18v-8M24 42v8M30 42v8M36 42v8M18 24h-8M18 30h-8M18 36h-8M42 24h8M42 30h8M42 36h8"/></svg>
      <h3>Cyber Security</h3>
      <p>Adipiscing elit sed autem eiusmode mporal laboratories dolore magna aliqua rerum adim minim veniam quis.</p>
    </div>
    <div class="service">
      <svg class="service-icon" width="60" height="60" viewBox="0 0 60 60" fill="none" stroke="#6b449b" stroke-width="2"><circle cx="26" cy="26" r="16"/><path d="M38 38l14 14"/><path d="M26 18v10M26 32v2"/></svg>
      <h3>Incident Response</h3>
      <p>Adipiscing elit sed autem eiusmode mporal laboratories dolore magna aliqua rerum adim minim veniam quis.</p>
    </div>
    <div class="service">
      <svg class="service-icon" width="60" height="60" viewBox="0 0 60 60" fill="none" stroke="#6b449b" stroke-width="2"><circle cx="30" cy="14" r="7"/><circle cx="12" cy="30" r="5"/><circle cx="48" cy="30" r="5"/><path d="M18 50c1-10 6-16 12-16s11 6 12 16M4 48c0-6 3-10 8-10M56 48c0-6-3-10-8-10"/></svg>
      <h3>Risk Assessment</h3>
      <p>Adipiscing elit sed autem eiusmode mporal laboratories dolore magna aliqua rerum adim minim veniam quis.</p>
    </div>
    <div class="service">
      <svg class="service-icon" width="60" height="60" viewBox="0 0 60 60" fill="none" stroke="#6b449b" stroke-width="2"><path d="M30 6l20 8v14c0 13-9 22-20 26C19 50 10 41 10 28V14z"/><rect x="23" y="27" width="14" height="11" rx="2"/><path d="M26 27v-4a4 4 0 0 1 8 0v4"/></svg>
      <h3>Network Security</h3>
      <p>Adipiscing elit sed autem eiusmode mporal laboratories dolore magna aliqua rerum adim minim veniam quis.</p>
    </div>
    <div class="service">
      <svg class="service-icon" width="60" height="60" viewBox="0 0 60 60" fill="none" stroke="#6b449b" stroke-width="2"><rect x="6" y="10" width="48" height="32" rx="2"/><path d="M22 52h16M30 42v10M22 26l6 6 12-12"/></svg>
      <h3>Managed Security Services</h3>
      <p>Adipiscing elit sed autem eiusmode mporal laboratories dolore magna aliqua rerum adim minim veniam quis.</p>
    </div>
  </div>
</section>

<section class="section products">
  <h2 class="section-title">Products</h2><span class="title-mark"></span>
  <div class="product-row">
    <div class="product-card">
      <div class="product-box" role="img" aria-label="Product 1 software box in white and teal" style="background:linear-gradient(120deg,#f4f6f6 0%,#f4f6f6 45%,#1fa8a8 46%,#178c8c)"></div>
      <div>
        <h3>PRODUCT 1</h3>
        <p>Morbi convallis bibendum urna ut viverra. Maecenas quis consequat libero, a feugiat eros. Nunc ut lacinia tortor morbi ultricies laoreet ullamcorper phasellus semper.</p>
        <span class="product-link">View Details →</span>
      </div>
    </div>
    <div class="product-card">
      <div class="product-box" role="img" aria-label="Product 2 software box in white and yellow" style="background:linear-gradient(120deg,#f4f6f6 0%,#f4f6f6 45%,#f5c319 46%,#e3ad06)"></div>
      <div>
        <h3>PRODUCT 2</h3>
        <p>Morbi convallis bibendum urna ut viverra. Maecenas quis consequat libero, a feugiat eros. Nunc ut lacinia tortor morbi ultricies laoreet ullamcorper phasellus semper.</p>
        <span class="product-link">View Details →</span>
      </div>
    </div>
  </div>
</section>

<section class="section callout">
  <div class="callout-visual" role="img" aria-label="Office team working at desks with laptops, framed in a rounded shape"></div>
  <div class="callout-copy">
    <h2>YOU NEED MORE SECURITY?</h2>
    <p class="lead">Aliquam sapien est, mollis id mattis id, scelerisque sed dolor.</p>
    <p>Proin accumsan erat sem, id porta risus dignissim ac. Vestibulum nec sapien in lacus ornare nec nec justo. Aliquam sapien est, mollis id mattis id, scelerisque sed dolor. Proin accumsan erat sem, id porta risus dignissim ac. Vestibulum nec sapien in lacus ornare nec nec justo.</p>
    <span class="cta"><i class="cta-square"></i>CONTACT US TODAY</span>
  </div>
</section>

<section class="section team">
  <h2 class="section-title">Our Team</h2><span class="title-mark"></span>
  <div class="team-row">
    <div class="member"><div class="member-photo" role="img" aria-label="Portrait photo of the founder"></div><h3>Marcus Delvane Orrick</h3><span>Founder &amp; CEO</span></div>
    <div class="member"><div class="member-photo" role="img" aria-label="Portrait photo of an associate"></div><h3>Elena Prewitt</h3><span>Associate</span></div>
    <div class="member"><div class="member-photo" role="img" aria-label="Portrait photo of a team member"></div><h3>Tomas Halberd</h3><span>Nisllacus</span></div>
    <div class="member"><div class="member-photo" role="img" aria-label="Portrait photo of a team member"></div><h3>Iris Calloway</h3><span>Nisllacus</span></div>
  </div>
  <div class="pager"><span></span><span class="on"></span></div>
</section>

<section class="section stats">
  <div class="stat-row">
    <div class="stat"><svg width="56" height="44" viewBox="0 0 56 44" fill="none" stroke="#f29a4b" stroke-width="2"><circle cx="28" cy="12" r="7"/><circle cx="10" cy="16" r="5"/><circle cx="46" cy="16" r="5"/><path d="M16 42c0-10 5-16 12-16s12 6 12 16M2 40c0-7 3-11 8-11M54 40c0-7-3-11-8-11"/></svg><strong>120</strong><span>About Employee</span></div>
    <div class="stat"><svg width="56" height="44" viewBox="0 0 56 44" fill="none" stroke="#f29a4b" stroke-width="2"><path d="M6 42h44M10 42V26h8v16M24 42V14h8v28M38 42V6h8v36"/></svg><strong>250</strong><span>Queries Solved</span></div>
    <div class="stat"><svg width="56" height="44" viewBox="0 0 56 44" fill="none" stroke="#f29a4b" stroke-width="2"><circle cx="28" cy="22" r="20"/><circle cx="28" cy="17" r="6"/><path d="M16 36c2-6 6-9 12-9s10 3 12 9"/></svg><strong>550</strong><span>Registered Users</span></div>
    <div class="stat"><svg width="56" height="44" viewBox="0 0 56 44" fill="none" stroke="#f29a4b" stroke-width="2"><circle cx="28" cy="22" r="20"/><circle cx="21" cy="18" r="1.5" fill="#f29a4b"/><circle cx="35" cy="18" r="1.5" fill="#f29a4b"/><path d="M19 27c4 6 14 6 18 0"/></svg><strong>1000</strong><span>Happy Customers</span></div>
  </div>
</section>

<section class="section reviews">
  <h2 class="section-title">Customer Reviews</h2>
  <div class="review side" style="left:90px">
    <div class="quote-mark">“</div><h3>Lorem Ipsum Dolor Sit Amet ...</h3>
    <p>Ut enim ad minim veniam dolor ullamco magna elit ut consectetur adipiscing. Expedita animi maiores aliquam fuit dis dolorem sunt.</p>
    <p class="who">Conrad Ashby</p><p class="role">Aliquam ligula</p>
  </div>
  <div class="review main">
    <div class="quote-mark">“</div><h3>Lorem Ipsum Dolor Sit Amet ...</h3>
    <p>Ut enim ad minim veniam dolor ullamco magna elit ut consectetur adipiscing. Expedita animi maiores aliquam fuit dis dolorem sunt fuga ut explicabo pariatur aut est repellat. Quo quis voluptas incididunt blandit consectetur sunt laudantium sed et.</p>
    <p class="who">Wren Hadley, Phasellum</p><p class="role">Quodis vulputat</p>
  </div>
  <div class="review side" style="left:810px">
    <div class="quote-mark">“</div><h3>Lorem Ipsum Dolor Sit Amet ...</h3>
    <p>Ut enim ad minim veniam dolor ullamco magna elit ut consectetur adipiscing. Expedita animi maiores aliquam fuit dis dolorem sunt.</p>
    <p class="who">Lena Morrow</p><p class="role">Aliquam ligula</p>
  </div>
  <svg style="position:absolute;left:400px;top:290px" width="10" height="16" viewBox="0 0 10 16"><path d="M8 2L2 8l6 6" fill="none" stroke="#555" stroke-width="2"/></svg>
  <svg style="position:absolute;left:790px;top:290px" width="10" height="16" viewBox="0 0 10 16"><path d="M2 2l6 6-6 6" fill="none" stroke="#555" stroke-width="2"/></svg>
</section>

<section class="section location">
  <div class="location-visual" role="img" aria-label="Dark photo of a business desk with laptop and documents, overlaid with network lines"></div>
  <h2>OUR LOCATION</h2>
  <p class="sub">Aliquam sapien est, mollis id mattis id, scelerisque sed dolor proin accumsan erat sem.</p>
  <div class="map" role="img" aria-label="Street map showing the corporate office location"></div>
  <svg style="position:absolute;left:430px;top:248px" width="24" height="34" viewBox="0 0 24 34"><path d="M12 33C4 21 2 17 2 12a10 10 0 0 1 20 0c0 5-2 9-10 21z" fill="#e2463c"/><circle cx="12" cy="12" r="4" fill="#fff"/></svg>
  <div class="help">
    <h3>NEED HELP?</h3>
    <small>Fill out the form below to get connected</small>
    <div class="field">Name *</div>
    <div class="field">Email *</div>
    <div class="field">Subject *</div>
    <div class="field">Message *</div>
    <span class="submit"><i></i>SUBMIT</span>
  </div>
</section>

<footer class="section site-footer">
  <span>COPYRIGHT © 2018 LUMERA FIELDWORKS. ALL RIGHTS RESERVED.</span>
  <div class="social"><span></span><span></span><span></span><span></span></div>
</footer>

</body>
</html>
```